Yacht, Boats, Watersports company needs a redesign of business card

Hello Designers!
We are a Boat dealership company that sells fun in the water, we sell boats, Yachts, Kayaks and also yacht WaterSport toys. We are looking to redesign our business cards in to something a little bit more sophisticated. in a way that we can make better use of our company colors. I'm attaching a zipped file containing the company 3 sets of company logo which one is an horizontal another one is a vertical and also a chromed 3d logo. Also is included two set of business cards that we use and also some designs that i think it's interesting. We use PMS 2026c Orange and PMS 7687C Blue. I would like to see at least two different options with the orange as accent and also using blue as an accent color. It's really important for the business cards to have a font option and size that is legible to most people. Our current website is wwww.coralpennant.com. Please visit if you want to have a better feeling of the Boat dealership
You can send Single sided or double side options. We are now using single sided but we may be open for a double side option if we really like the design.
Target Market(s)
Marine, boat sales, yacht sales, water toys sales/
Contact Information for Business Card
Name: Dale Whitcombe
Address: 212 North Fenwick Lane,
Harbor Key, FL 33091
Phone: 954-731-8842
Fax: 954:731-8843
Cell: 954-382-1490
Email: dw@coralpennant.com
Website: coralpennant.com
Requirements
Must have
- the current information of the business card provided.
logo
use the PMS Colors
Nice to have
- a touch of elegance and sophistication but simple
Should not have
- should not have any typography that is hard to read, the card should be simple but yet sophisticated.

```html
<!DOCTYPE html>
<html lang="en">
<head>
<meta charset="utf-8">
<title>Coral Pennant – Business Card</title>
<link href="https://fonts.googleapis.com/css2?family=Poppins:wght@400;600;700&display=swap" rel="stylesheet">
<style>
  :root {
    --page-bg: #e4e4e4;
    --card-white: #ffffff;
    --brand-blue: #1f65ad;
    --brand-blue-light: #4b9bd2;
    --brand-blue-dark: #1a58a0;
    --brand-orange: #ef862a;
    --brand-orange-light: #f4a552;
    --text-light: #ffffff;
  }
  * { margin: 0; padding: 0; box-sizing: border-box; }
  html, body { width: 1200px; height: 1200px; overflow: hidden; }
  body {
    background: var(--page-bg);
    font-family: "Poppins", sans-serif;
    position: relative;
  }
  .card {
    position: absolute;
    left: 262px;
    width: 686px;
    height: 392px;
    border-radius: 22px;
    overflow: hidden;
  }
  .card--front { top: 165px; background: var(--card-white); }
  .card--back {
    top: 653px;
    background: linear-gradient(20deg, var(--brand-blue-dark) 0%, var(--brand-blue) 55%, var(--brand-blue-light) 100%);
  }
  .card__bg { position: absolute; inset: 0; width: 100%; height: 100%; }

  .brand-lockup {
    position: absolute;
    left: 31px;
    top: 40px;
    width: 270px;
    text-align: center;
  }
  .brand-lockup__dot {
    display: block;
    width: 68px; height: 68px;
    margin: 0 auto 22px;
    border-radius: 50%;
    border: 5px solid var(--brand-blue);
  }
  .brand-lockup__name {
    font-weight: 700;
    font-size: 25px;
    letter-spacing: 0.5px;
    color: var(--brand-blue);
    white-space: nowrap;
  }

  .contact {
    position: absolute;
    right: 51px;
    top: 168px;
    text-align: right;
    color: var(--text-light);
  }
  .contact__name {
    font-weight: 600;
    font-size: 22px;
    color: var(--brand-orange);
    letter-spacing: 0.3px;
    line-height: 1.2;
  }
  .contact__address {
    margin-top: 9px;
    font-size: 16.5px;
    line-height: 19px;
  }
  .contact__list { list-style: none; margin-top: 12px; }
  .contact__item {
    display: flex;
    justify-content: flex-end;
    align-items: center;
    gap: 8px;
    font-size: 16px;
    line-height: 19.4px;
  }
  .contact__icon { width: 13px; height: 13px; fill: var(--brand-orange); flex: none; }

  .back-mark {
    position: absolute;
    left: 216px; top: 60px;
    width: 254px; height: 254px;
    border-radius: 50%;
    border: 12px solid var(--text-light);
    display: flex; align-items: center; justify-content: center;
  }
  .back-mark__name {
    font-weight: 700;
    font-size: 27px;
    color: var(--text-light);
    letter-spacing: 0.5px;
    text-align: center;
    line-height: 1.15;
  }
  .back-url {
    position: absolute;
    left: 0; right: 0;
    top: 343px;
    text-align: center;
    font-size: 16.5px;
    letter-spacing: 3.4px;
    color: var(--text-light);
  }
</style>
</head>
<body>

<section class="card card--front">
  <svg class="card__bg" viewBox="0 0 800 457" preserveAspectRatio="none" aria-hidden="true">
    <defs>
      <linearGradient id="front-blue" x1="0" y1="1" x2="1" y2="0">
        <stop offset="0" stop-color="#1a5aa3"/>
        <stop offset="0.6" stop-color="#2a72b8"/>
        <stop offset="1" stop-color="#4f9fd4"/>
      </linearGradient>
      <linearGradient id="front-orange" x1="0" y1="1" x2="1" y2="0">
        <stop offset="0" stop-color="#ec7a1e"/>
        <stop offset="1" stop-color="#f5ac5c"/>
      </linearGradient>
    </defs>
    <polygon points="682,0 800,0 800,457 106,457" fill="url(#front-blue)"/>
    <polygon points="650,0 682,0 106,457 88,457" fill="url(#front-orange)"/>
  </svg>

  <div class="brand-lockup">
    <span class="brand-lockup__dot"></span>
    <div class="brand-lockup__name">CORAL PENNANT</div>
  </div>

  <div class="contact">
    <h1 class="contact__name">DALE WHITCOMBE</h1>
    <p class="contact__address">212 North Fenwick Lane<br>Harbor Key, FL 33091</p>
    <ul class="contact__list">
      <li class="contact__item">954-731-8842
        <svg class="contact__icon" viewBox="0 0 16 16"><path d="M3.5 1l2.5 3-1.5 1.8c.8 2 2.3 3.6 4.3 4.5L10.6 8.8l3.4 2.3-1.2 3C7 14 2 9 1.8 3z"/></svg>
      </li>
      <li class="contact__item">954-382-1490
        <svg class="contact__icon" viewBox="0 0 16 16"><path d="M4 0h8a1 1 0 0 1 1 1v14a1 1 0 0 1-1 1H4a1 1 0 0 1-1-1V1a1 1 0 0 1 1-1zm1 2v10h6V2zm3 11a1 1 0 1 0 0 2 1 1 0 0 0 0-2z"/></svg>
      </li>
      <li class="contact__item">954-731-8843
        <svg class="contact__icon" viewBox="0 0 16 16"><path d="M4 1h7l1 1v4H4zM1 7h14v6h-2v2H3v-2H1zm4 3v4h6v-4z"/></svg>
      </li>
      <li class="contact__item">dw@coralpennant.com
        <svg class="contact__icon" viewBox="0 0 16 16"><path d="M1 3h14v1L8 9 1 4zm0 3l7 5 7-5v7H1z"/></svg>
      </li>
      <li class="contact__item">coralpennant.com
        <svg class="contact__icon" viewBox="0 0 16 16"><circle cx="8" cy="8" r="7"/><path d="M4 5c2 0 2 2 4 2s1 3 3 3M9 2c0 2 3 2 4 4" stroke="#2a72b8" stroke-width="1.3" fill="none"/></svg>
      </li>
    </ul>
  </div>
</section>

<section class="card card--back">
  <div class="back-mark">
    <div class="back-mark__name">CORAL<br>PENNANT</div>
  </div>
  <p class="back-url">WWW.CORALPENNANT.COM</p>
</section>

</body>
</html>
```